Brand new letterhead, business card, email signature etc.

We are a financial company in London, UK. Our website is www.marlowvane.com. We're wanting a complete remodel of the company colours, letter head, business cards, email signatures, etc. Looking to keep the same font for the company name. I have upload a colour palette that we want to work with. We're looking for company letterhead for outgoing letters/ correspondence, letterhead for internal documentation, email signatures, e-letters. etc. Ultimately we will redesign the entire website also. It is important that our clients get a strong, secure, warm, trustworthy, solid feeling and first impression.
Updates

Designs look the same

Target Market(s)

Institutional investors, (ultra) high net worth individuals

Industry/Entity Type

Finance, Invesments banking.

Font styles to use
Other font styles liked:
• Current font is "Champagne & Limousines"

Requirements
Must have
• Must use the colours provided on the PDF uploaded to the portal. The purple = main colour. The red = accent colour.
Nice to have
• Nice to use same font as now for the company name "Corvane". Font is "Champagne & Limousines". Nice to have some reference to the old logo flower, but only subtle.
Should not have
• Do not use the colour red from our website. Use the colours provided on the colour palette PDF that I uploaded in the portal.

```html
<!DOCTYPE html>
<html lang="en">
<head>
<meta charset="utf-8">
<title>Corvane Stationery</title>
<link href="https://fonts.googleapis.com/css2?family=Quicksand:wght@400;500&family=Ubuntu:wght@500&display=swap" rel="stylesheet">
<style>
  :root{
    --stage:#d3d3d5;
    --paper:#f4f4f4;
    --paper-white:#ffffff;
    --plum:#1e0a1c;
    --red:#d42e24;
    --ink:#1b1b1b;
  }
  *{margin:0;padding:0;box-sizing:border-box}
  html,body{width:1200px;height:792px;overflow:hidden;background:var(--stage)}
  body{position:relative;font-family:"Quicksand",sans-serif;color:var(--ink)}
  .sheet{position:absolute;background:var(--paper);overflow:hidden}
  .corner{position:absolute;display:block}
  .band{position:absolute;background:var(--plum)}
  .mark{position:absolute;display:flex;align-items:center}
  .mark-square{border:1px solid var(--ink);flex:none}
  .wordmark{font-family:"Quicksand",sans-serif;font-weight:400;letter-spacing:.22em;color:var(--ink);white-space:nowrap}
  .divider{position:absolute;width:1px;background:var(--ink)}
  .person-name{font-family:"Ubuntu",sans-serif;font-weight:500;color:var(--ink);white-space:nowrap}
  .person-name .first{color:var(--red)}
  .contact{list-style:none}
  .contact li{display:flex;align-items:center;white-space:nowrap}
  .icon{flex:none;fill:var(--red)}

  /* business card front */
  .card-front{left:154px;top:233px;width:195px;height:111px}
  .card-front .mark{left:22px;top:40px;gap:4px}
  .card-front .mark-square{width:8px;height:8px}
  .card-front .wordmark{font-size:9px}
  .card-front .divider{left:99px;top:19px;height:55px}
  .card-front .identity{position:absolute;left:114px;top:22px}
  .card-front .person-name{font-size:9.5px}
  .card-front .role{font-size:5px;margin-top:1px}
  .card-front .contact{position:absolute;left:114px;top:49px;font-size:5px;line-height:7.2px}
  .card-front .contact .icon{width:5px;height:5px;margin-right:3px}
  .card-front .address{position:absolute;left:0;right:0;top:88px;text-align:center;font-size:5px}

  /* business card back */
  .card-back{left:379px;top:233px;width:195px;height:111px}
  .card-back .mark{left:33px;top:39px;gap:8px}
  .card-back .mark-square{width:32px;height:32px}
  .card-back .wordmark{font-size:17px}

  /* email signature */
  .signature{left:153px;top:401px;width:420px;height:139px;background:var(--paper-white)}
  .signature .mark{left:17px;top:46px;gap:10px}
  .signature .mark-square{width:41px;height:41px}
  .signature .wordmark{font-size:21px}
  .signature .divider{left:210px;top:20px;height:93px}
  .signature .identity{position:absolute;left:231px;top:21px}
  .signature .person-name{font-size:14px}
  .signature .role,.signature .address{font-size:8px;line-height:10px}
  .signature .address{margin-top:7px}
  .signature .contact{position:absolute;left:231px;top:80px;font-size:8px;line-height:10.2px}
  .signature .contact .icon{width:7px;height:7px;margin-right:4px}

  /* letterhead */
  .letterhead{left:595px;top:132px;width:367px;height:518px}
  .letterhead .mark{left:22px;top:8px;gap:9px}
  .letterhead .mark-square{width:39px;height:39px}
  .letterhead .wordmark{font-size:20px}
  .letterhead .contact{position:absolute;right:15px;top:444px;font-size:7.8px;line-height:10px;text-align:right}
  .letterhead .contact li{justify-content:flex-end}
  .letterhead .contact .icon{width:7px;height:7px;margin-left:6px}
  .letterhead .contact .gap{margin-top:6px}
</style>
</head>
<body>

<!-- business card front -->
<section class="sheet card-front">
  <svg class="corner" style="left:0;top:0" width="14" height="14" viewBox="0 0 14 14"><polygon points="0,0 14,0 0,14" fill="var(--red)"/></svg>
  <div class="band" style="left:0;bottom:0;width:100%;height:3px"></div>
  <svg class="corner" style="right:0;bottom:0" width="40" height="42" viewBox="0 0 40 42"><polygon points="40,0 40,42 0,42" fill="var(--plum)"/><polygon points="40,5 40,42 5,42" fill="var(--red)"/></svg>
  <div class="mark"><span class="mark-square"></span><span class="wordmark">CORVANE</span></div>
  <div class="divider"></div>
  <div class="identity">
    <p class="person-name"><span class="first">Elena</span> Hartwell</p>
    <p class="role">Managing Director</p>
  </div>
  <ul class="contact">
    <li><svg class="icon" viewBox="0 0 10 10"><path d="M2 1l2 2-1 1.5a6 6 0 0 0 2.5 2.5L7 6l2 2-1.5 1.5C4 9 1 6 .5 2.5z"/></svg>(020) 7946 0318</li>
    <li><svg class="icon" viewBox="0 0 10 10"><path d="M0 2h10v6H0z M0 2l5 3.5L10 2" fill="none" stroke="var(--red)" stroke-width="1.4"/></svg>info@marlowvane.com</li>
    <li><svg class="icon" viewBox="0 0 10 10"><circle cx="5" cy="5" r="4.5"/></svg>www.marlowvane.com</li>
  </ul>
  <p class="address">18 Aldgate Row, Suite 4, London EC3N 1AH</p>
</section>

<!-- business card back -->
<section class="sheet card-back">
  <div class="band" style="left:0;top:0;width:100%;height:4px"></div>
  <svg class="corner" style="left:0;top:0" width="42" height="46" viewBox="0 0 42 46"><polygon points="0,0 42,0 0,46" fill="var(--plum)"/><polygon points="0,0 37,0 0,41" fill="var(--red)"/></svg>
  <svg class="corner" style="right:0;bottom:0" width="10" height="10" viewBox="0 0 10 10"><polygon points="10,0 10,10 0,10" fill="var(--red)"/></svg>
  <div class="mark"><span class="mark-square"></span><span class="wordmark">CORVANE</span></div>
</section>

<!-- email signature -->
<section class="sheet signature">
  <svg class="corner" style="right:0;top:0" width="26" height="26" viewBox="0 0 26 26"><polygon points="0,0 26,0 26,26" fill="var(--red)"/></svg>
  <div class="band" style="left:0;bottom:0;width:100%;height:4px"></div>
  <svg class="corner" style="left:0;bottom:0" width="38" height="44" viewBox="0 0 38 44"><polygon points="0,0 38,44 0,44" fill="var(--plum)"/><polygon points="0,4 34,44 0,44" fill="var(--red)"/></svg>
  <div class="mark"><span class="mark-square"></span><span class="wordmark">CORVANE</span></div>
  <div class="divider"></div>
  <div class="identity">
    <p class="person-name"><span class="first">Elena</span> Hartwell</p>
    <p class="role">Managing Director</p>
    <p class="address">18 Aldgate Row, Suite 4<br>London EC3N 1AH</p>
  </div>
  <ul class="contact">
    <li><svg class="icon" viewBox="0 0 10 10"><path d="M2 1l2 2-1 1.5a6 6 0 0 0 2.5 2.5L7 6l2 2-1.5 1.5C4 9 1 6 .5 2.5z"/></svg>(020) 7946 0318</li>
    <li><svg class="icon" viewBox="0 0 10 10"><path d="M0 2h10v6H0z M0 2l5 3.5L10 2" fill="none" stroke="var(--red)" stroke-width="1.4"/></svg>info@marlowvane.com</li>
    <li><svg class="icon" viewBox="0 0 10 10"><circle cx="5" cy="5" r="4.5"/></svg>www.marlowvane.com</li>
  </ul>
</section>

<!-- letterhead -->
<section class="sheet letterhead">
  <div class="band" style="left:0;top:0;width:10px;height:100%"></div>
  <svg class="corner" style="right:0;top:0" width="53" height="53" viewBox="0 0 53 53"><polygon points="0,0 53,0 53,53" fill="var(--red)"/></svg>
  <svg class="corner" style="left:0;bottom:0" width="96" height="84" viewBox="0 0 96 84"><polygon points="0,0 96,84 0,84" fill="var(--plum)"/><polygon points="0,10 84,84 0,84" fill="var(--red)"/></svg>
  <div class="mark"><span class="mark-square"></span><span class="wordmark">CORVANE</span></div>
  <ul class="contact">
    <li>72 Hollin Lane<svg class="icon" viewBox="0 0 10 10"><path d="M5 0a3.5 3.5 0 0 1 3.5 3.5C8.5 6 5 10 5 10S1.5 6 1.5 3.5A3.5 3.5 0 0 1 5 0z"/></svg></li>
    <li style="margin-right:13px">Southwark, London, SE1 4QT</li>
    <li class="gap">(020) 7946 0318<svg class="icon" viewBox="0 0 10 10"><path d="M2 1l2 2-1 1.5a6 6 0 0 0 2.5 2.5L7 6l2 2-1.5 1.5C4 9 1 6 .5 2.5z"/></svg></li>
    <li>www.marlowvane.com<svg class="icon" viewBox="0 0 10 10"><circle cx="5" cy="5" r="4.5"/></svg></li>
    <li>hello@marlowvane.com<svg class="icon" viewBox="0 0 10 10"><path d="M0 2h10v6H0z M0 2l5 3.5L10 2" fill="none" stroke="var(--red)" stroke-width="1.4"/></svg></li>
  </ul>
</section>

</body>
</html>
```